Lumen Harbor is a Smart Device and Wiring Business offering the latest in Smart Home Devices inc

Looking for a new website to draw people to my business and explain what a smart home is all about. I currently own a domain and have a website I put together in webquill business website builder. address www.lumenharbor.example. The website needs modernising and be visually appealing with cool action buttons, client feedback page etc.

The webpage needs to present an image of seamless integration of wireless voice control and smart devices that take tasks and activities away from the owner saving them time and money.

I have a facebook business page(lumen harbor) and instagram linked with the business, are we able to link this to the website somehow?

Target Market(s)

Residential home owners who want to modernise their home. Who have seen adverts for corvo hub and pellar mira and want to put it in their home.

Industry/Entity Type

Technology Equipment

Number of Pages Required

1 page

Colors

Designer to choose colors to be used in the design.

Requirements
Must have
• A great landing page, that is modern and attractive, that gets across the idea of smart devices and technology.
• Must be ios/android device friendly.
Nice to have
• interactive/animated buttons
• I like the direction and interactiveness of these websites, a simplified version would be awesome.
• Something in between:
• http://www.quorbeliving.example/ and https://plindo.example/
• http://www.quorbeliving.example/

```html
<!DOCTYPE html>
<html lang="en">
<head>
<meta charset="utf-8">
<title>Lumen Harbor – Smart Device Integration</title>
<link href="https://fonts.googleapis.com/css2?family=Lato:wght@300;400;700;900&display=swap" rel="stylesheet">
<style>
:root{
  --blue:#2a86c7;
  --blue-dark:#1f6fa8;
  --ink:#3a3a3a;
  --muted:#8a8a8a;
  --dark:#2b2b2b;
  --darker:#1e1e1e;
  --light:#f3f3f3;
  --line:#dcdcdc;
  --white:#ffffff;
}
*{box-sizing:border-box;margin:0;padding:0}
html,body{width:1200px;height:3200px;overflow:hidden}
body{font-family:"Lato",sans-serif;color:var(--ink);background:var(--white);position:relative}
section,header,footer{position:absolute;left:0;width:1200px}

.topbar{top:0;height:36px;background:var(--darker);color:#cfcfcf;font-size:13px;display:flex;align-items:center;justify-content:space-between;padding:0 40px}
.topbar .social{display:flex;gap:14px}
.topbar .social span{width:14px;height:14px;border-radius:50%;background:#9a9a9a;display:block}
.topbar .contact{display:flex;gap:40px;align-items:center}
.topbar .contact span{display:flex;align-items:center;gap:8px}

.site-header{top:36px;height:120px;background:var(--white);border-bottom:1px solid var(--line);text-align:center}
.brand{display:inline-flex;align-items:center;gap:12px;margin-top:20px}
.brand-mark{width:40px;height:40px;border-radius:50%;background:var(--blue)}
.brand-name{font-size:30px;font-weight:700;color:var(--blue);letter-spacing:1px;text-transform:uppercase}
.nav{display:flex;justify-content:center;gap:34px;margin-top:16px;font-size:12px;font-weight:700;letter-spacing:.5px}
.nav a{color:var(--ink);text-decoration:none;padding-bottom:4px}
.nav a.active{color:var(--blue);border-bottom:2px solid var(--blue)}

.hero{top:156px;height:534px;background:linear-gradient(115deg,#f6f6f6 0%,#f6f6f6 55%,#ececec 55%,#e6e6e6 100%)}
.hero h1{position:absolute;left:76px;top:170px;font-size:46px;line-height:54px;font-weight:700;color:var(--blue);letter-spacing:1px}
.hero p{position:absolute;left:76px;top:300px;width:420px;font-size:16px;line-height:26px;color:#555}
.hero .visual{position:absolute;left:560px;top:60px;width:470px;height:420px;border-radius:6px;background:radial-gradient(circle at 50% 45%,#4a4a4a,#151515 70%)}

.welcome{top:690px;height:310px;background:linear-gradient(#3a3a3a,#262626);color:#e4e4e4;text-align:center}
.welcome h2{margin-top:56px;font-size:40px;font-weight:400;letter-spacing:2px;color:var(--white)}
.welcome p{width:760px;margin:24px auto 0;font-size:14px;line-height:22px;color:#cfcfcf}
.welcome p+p{margin-top:16px}

.section-title{font-size:32px;font-weight:700;color:var(--blue);letter-spacing:1px}
.process{top:1040px;height:500px}
.process .label{position:absolute;left:72px;top:50px;font-size:18px;font-weight:900;color:var(--blue)}
.process svg.steps{position:absolute;left:72px;top:100px}
.steps text{font-family:"Lato",sans-serif}
.what{position:absolute;left:680px;top:90px;width:440px}
.what h2{font-size:44px;font-weight:400;color:var(--blue);letter-spacing:1px}
.what p{margin-top:18px;font-size:14px;line-height:22px;color:#666}
.btn{display:inline-block;background:var(--blue);color:var(--white);font-weight:700;font-size:14px;letter-spacing:1px;padding:12px 36px;border-radius:24px;text-transform:uppercase}
.what .btn{margin-top:22px}

.specialist{top:1560px;height:540px;background:var(--light)}
.specialist .section-title{position:absolute;left:72px;top:50px;font-size:40px}
.arrows{position:absolute;right:90px;top:56px;display:flex;gap:8px}
.arrows span{width:34px;height:34px;background:var(--blue);display:flex;align-items:center;justify-content:center}
.cards{position:absolute;left:72px;top:120px;display:flex;gap:30px}
.card{width:332px;height:390px;background:var(--white);box-shadow:0 2px 8px rgba(0,0,0,.08);position:relative}
.card .photo{height:190px}
.card .badge{position:absolute;right:20px;top:166px;width:48px;height:48px;border-radius:50%;background:var(--white);border:2px solid var(--blue);display:flex;align-items:center;justify-content:center}
.card h3{margin:30px 24px 0;font-size:21px;font-weight:700;color:var(--blue)}
.card p{margin:12px 24px 0;font-size:13px;line-height:20px;color:#777}
.card .more{display:inline-block;margin:16px 24px 0;font-size:13px;font-weight:700;color:var(--blue);border-bottom:2px solid var(--blue)}

.testimonials{top:2140px;height:330px;background:linear-gradient(#333,#1f1f1f);color:var(--white)}
.testimonials h2{text-align:center;margin-top:40px;font-size:40px;font-weight:400;letter-spacing:2px}
.quote{position:absolute;left:200px;top:130px;display:flex;gap:36px;width:800px}
.quote .avatar{flex:none;width:110px;height:110px;border-radius:50%;background:linear-gradient(#d9b79a,#8c6a52);border:3px solid var(--white)}
.quote p{font-size:14px;line-height:22px;color:#d6d6d6}
.quote .who{margin-top:12px;font-size:13px;font-weight:700;letter-spacing:1px;color:var(--white)}
.dots{position:absolute;left:0;width:1200px;top:290px;display:flex;justify-content:center;gap:8px}
.dots span{width:9px;height:9px;border-radius:50%;border:1px solid var(--white)}
.dots span.on{background:var(--white)}

.contact{top:2470px;height:330px;background:var(--white)}
.form{position:absolute;left:120px;top:50px;width:960px;height:260px;box-shadow:0 2px 14px rgba(0,0,0,.1);background:var(--white)}
.field{position:absolute;border-bottom:1px solid var(--line);font-size:13px;color:var(--muted);padding-bottom:8px}
.form .btn{position:absolute;left:430px;top:196px;padding:10px 44px}

.map{top:2800px;height:360px;background:linear-gradient(135deg,#e7ecdf,#dfe6ee)}
.map .pin{position:absolute;left:780px;top:140px}
.footer{top:3160px;height:40px;background:var(--darker);color:#bdbdbd;font-size:12px;text-align:center;line-height:40px;letter-spacing:.5px}
</style>
</head>
<body>

<div class="topbar" style="position:absolute;left:0;width:1200px">
  <div class="social"><span></span><span></span><span></span><span></span></div>
  <div class="contact">
    <span><svg width="12" height="14" viewBox="0 0 12 14"><path d="M6 0a5 5 0 0 0-5 5c0 4 5 9 5 9s5-5 5-9a5 5 0 0 0-5-5zm0 7a2 2 0 1 1 0-4 2 2 0 0 1 0 4z" fill="#cfcfcf"/></svg>Northgate, Lakeview WA, Australia</span>
    <span><svg width="14" height="10" viewBox="0 0 14 10"><rect x=".5" y=".5" width="13" height="9" fill="none" stroke="#cfcfcf"/><path d="M.5.5 7 6 13.5.5" fill="none" stroke="#cfcfcf"/></svg>info@lumenharbor.example</span>
  </div>
</div>

<header class="site-header">
  <div class="brand"><span class="brand-mark"></span><span class="brand-name">Lumen Harbor</span></div>
  <nav class="nav">
    <a class="active">HOME</a><a>ABOUT US</a><a>PRODUCTS</a><a>WHAT WE DO</a><a>CONTACT US</a>
  </nav>
</header>

<section class="hero">
  <h1>SMART DEVICE<br>INTEGRATION</h1>
  <p>We are focused on delivering affordable and easily usable devices for your home and office</p>
  <div class="visual" role="img" aria-label="Black smart home speaker system with subwoofer and satellite speakers"></div>
</section>

<section class="welcome">
  <h2>WELCOME TO LUMEN HARBOR</h2>
  <p>Lumen Harbor began as an idea in a garage and a belief that home technology should be easily accessible and reasonably priced. We are constantly sourcing and experimenting with new technologies and solutions to create any vision of the future you can imagine.</p>
  <p>Our founder, who is passionate about all things tech, has experimented for years with newly emerging smart devices, purchasing and installing them in and around his home in a quest to find the perfect balance of convenient, reliable and smart technology.</p>
</section>

<section class="process">
  <div class="label">THE PROCESS</div>
  <svg class="steps" width="520" height="330" viewBox="0 0 520 330">
    <rect x="0" y="20" width="80" height="280" rx="10" fill="#e9e9e9"/>
    <path d="M70 30 C200 40 210 290 70 300" fill="none" stroke="#d8d8d8" stroke-width="2"/>
    <g font-size="14" fill="#555">
      <circle cx="160" cy="70" r="18" fill="#2a86c7"/><text x="160" y="75" text-anchor="middle" fill="#fff" font-weight="700">01</text><text x="200" y="75">Consultation</text>
      <circle cx="190" cy="140" r="18" fill="#2a86c7"/><text x="190" y="145" text-anchor="middle" fill="#fff" font-weight="700">02</text><text x="230" y="145">Installation</text>
      <circle cx="190" cy="210" r="18" fill="#2a86c7"/><text x="190" y="215" text-anchor="middle" fill="#fff" font-weight="700">03</text><text x="230" y="215">Finalisation</text>
      <circle cx="160" cy="275" r="18" fill="#2a86c7"/><text x="160" y="280" text-anchor="middle" fill="#fff" font-weight="700">04</text><text x="200" y="280">Support</text>
    </g>
  </svg>
  <div class="what">
    <h2>WHAT WE DO</h2>
    <p>We are a small group of local tech consultants, with long-term experience in the integration, setup and fault finding of advanced technologies, so we are passionate about the products we sell and confident in the service we provide.</p>
    <p>Our aim is to simplify the mystery and confusion surrounding smart devices and connected products, and incorporate them into your busy, making them easier and more time rich.</p>
    <span class="btn">Know More</span>
  </div>
</section>

<section class="specialist">
  <h2 class="section-title">SMART HOME SPECIALIST</h2>
  <div class="arrows">
    <span><svg width="10" height="12" viewBox="0 0 10 12"><path d="M8 1 2 6l6 5" fill="none" stroke="#fff" stroke-width="2"/></svg></span>
    <span><svg width="10" height="12" viewBox="0 0 10 12"><path d="M2 1l6 5-6 5" fill="none" stroke="#fff" stroke-width="2"/></svg></span>
  </div>
  <div class="cards">
    <article class="card">
      <div class="photo" role="img" aria-label="Hand holding a phone controlling home automation" style="background:linear-gradient(135deg,#3d5566,#9fb3c2)"></div>
      <span class="badge"><svg width="20" height="20" viewBox="0 0 20 20"><path d="M3 10 10 3l7 7v7H3z" fill="none" stroke="#2a86c7" stroke-width="2"/></svg></span>
      <h3>Home Automation</h3>
      <p>Book us your future and we'll create reality, by bringing technology into your home.</p>
      <span class="more">READ MORE</span>
    </article>
    <article class="card">
      <div class="photo" role="img" aria-label="Modern living room with a smart speaker" style="background:linear-gradient(135deg,#8a7a68,#d8cdbf)"></div>
      <span class="badge"><svg width="20" height="20" viewBox="0 0 20 20"><rect x="7" y="2" width="6" height="10" rx="3" fill="none" stroke="#2a86c7" stroke-width="2"/><path d="M4 10a6 6 0 0 0 12 0M10 16v3" fill="none" stroke="#2a86c7" stroke-width="2"/></svg></span>
      <h3>Voice Control With Mira</h3>
      <p>Your own concierge in a box, control your home devices, lights and music.</p>
      <span class="more">READ MORE</span>
    </article>
    <article class="card">
      <div class="photo" role="img" aria-label="Home theatre room with large screen and seating" style="background:linear-gradient(135deg,#2a2438,#7a5a46)"></div>
      <span class="badge"><svg width="20" height="20" viewBox="0 0 20 20"><rect x="2" y="4" width="16" height="10" fill="none" stroke="#2a86c7" stroke-width="2"/><path d="M7 17h6" stroke="#2a86c7" stroke-width="2"/></svg></span>
      <h3>Home Theatre Design</h3>
      <p>With market beyond options, from frontyard to boundless, we design it all.</p>
      <span class="more">READ MORE</span>
    </article>
  </div>
</section>

<section class="testimonials">
  <h2>TESTIMONIALS</h2>
  <div class="quote">
    <div class="avatar" role="img" aria-label="Client portrait"></div>
    <div>
      <p>Lorem Ipsum is simply dummy text of the printing and typesetting industry. Lorem Ipsum has been the industry's standard dummy text ever since the 1500s, when an unknown printer took a galley of type and scrambled it to make a type specimen book. It has survived not only five centuries.</p>
      <div class="who">— CLIENT NAME</div>
    </div>
  </div>
  <div class="dots"><span class="on"></span><span></span><span></span></div>
</section>

<section class="contact">
  <div class="form">
    <div class="field" style="left:40px;top:40px;width:270px">Your Name</div>
    <div class="field" style="left:345px;top:40px;width:270px">Your Email</div>
    <div class="field" style="left:650px;top:40px;width:270px">Your phone no.</div>
    <div class="field" style="left:40px;top:110px;width:880px;height:60px">Your Message</div>
    <span class="btn">Send</span>
  </div>
</section>

<section class="map" role="img" aria-label="Street map showing the business location">
  <svg class="pin" width="28" height="40" viewBox="0 0 28 40"><path d="M14 0a14 14 0 0 0-14 14c0 10 14 26 14 26s14-16 14-26A14 14 0 0 0 14 0z" fill="#2a86c7"/><circle cx="14" cy="14" r="5" fill="#fff"/></svg>
</section>

<footer class="footer">©LUMEN HARBOR, 2018 . All Rights Reserved.</footer>

</body>
</html>
```